Coral Wing Flights brochure

A single A4 brochures that is tri-folded and shows some of our tour packages with contact details.

Please visit www.coralwingflights.com.au to see the designs and images that can be used.

I want to provide designers the freedom to try something creative because I want to give prospective client - normally tourists to Sydney a quality service. I want the brochure to reflect this.

The image on the front page needs to be of the Sydney Harbour. The image MUST be in daylight - not night time.

I have now provided an image of the aircraft (in GIF format). Please use this image and place it over the image of the sydney harbour bridge and quayside concert pavilion.

I may need to discuss this further but what I have not show in the attached files is a small form I will like the client to fill out..

Reservation number
Name
Address
Phone number
Email

We can discuss this at a latter time.

The QR Code needs to contain your web address (www.coralwingflights.com.au)

Target Market(s)

Visitors and tourists to Sydney who want a day trip.
We are providing an exciting way to see Sydney. By air in a light aircraft...

Industry/Entity Type

House

Font styles to use
Sans Serif
Script

Colors
33a6d7
3276b5
85acd3
85cae6
ffffff

Requirements
Must have
• Brochure must be A4 (with about 2 to 3mm bleed - so it can be cut at the printers). They but be folded in 3 to produce a DL size brochure.

The words "Prepare to be amazed" should be in script font...

Please use the following wording for our Terms can conditions...

Terms and Conditions
Coral Wing Flights operates from Merrowdale Airfield within Sydney’s busy airspace Your chosen flight may be subject to delays. Clearance to enter controlled airspace may be refused - this is especially true of our popular Coastline Panorama flight. If this happens, we can either offer other suitable flights, reschedule the flight or, if this isn’t suitable, we provide a refund.
Other aircraft, besides our standard Talbin Skyrunners, are available if we consider they better suit your requirements.
See our web site www.coralwingflights.com.au for full details.
Coral Wing Flights is a trading name of Orvexa Pty Limited
(ABN 81 417 286 309) which operates under the Air Operators Certificate (AOC) of Dorrigan and Welsford Pty Ltd.
Nice to have
• Suggestion - on one of the sides (with the packages) to have a background image.

Suggestion is to keep the brochure light and "airy"

```html
<!DOCTYPE html>
<html lang="en">
<head>
<meta charset="utf-8">
<title>Coral Wing Flights – Tour Packages</title>
<link href="https://fonts.googleapis.com/css2?family=Open+Sans:wght@300;400;700&family=Damion&display=swap" rel="stylesheet">
<style>
  :root {
    --sky: #33a6d7;
    --deep: #3276b5;
    --mist: #85acd3;
    --pale: #85cae6;
    --white: #ffffff;
    --ink: #111111;
  }
  html, body { margin: 0; padding: 0; overflow: hidden; background: var(--white); }
  .spread {
    position: relative;
    width: 1200px; height: 849px;
    overflow: hidden;
    background: var(--sky);
    font-family: "Open Sans", Arial, sans-serif;
    color: var(--white);
  }
  .intro-strip {
    position: absolute; left: 0; top: 0; width: 1200px; height: 104px;
    background: var(--white);
    border-bottom: 2px solid var(--sky);
  }
  .intro {
    position: absolute; top: 17px; width: 380px; margin: 0;
    font-family: "Damion", "Brush Script MT", cursive;
    font-size: 14px; line-height: 18.5px;
    white-space: nowrap;
    color: var(--ink); text-align: center;
  }
  .photo { position: absolute; top: 113px; height: 270px; }
  .photo--harbour { left: 0; width: 398px; background: linear-gradient(160deg, #bcd6e8 0%, #4c86a3 35%, #1f5a66 70%, #2a4f5a 100%); }
  .photo--beach { left: 400px; width: 400px; background: linear-gradient(180deg, #3f8fd8 0%, #9cc6e6 28%, #e7e2d6 50%, #4aa0c8 62%, #5f8f3a 85%, #3d6a2a 100%); }
  .photo--cliffs { left: 802px; width: 398px; background: linear-gradient(160deg, #6f7d6a 0%, #a9612a 35%, #c9772f 55%, #5a3a1e 80%, #3a3020 100%); }
  .wave { position: absolute; left: 0; top: 320px; width: 1200px; height: 110px; }
  .facts { position: absolute; top: 436px; margin: 0; padding: 0; list-style: none; font-size: 13.5px; line-height: 23px; }
  .facts li { display: flex; align-items: center; gap: 5px; white-space: nowrap; }
  .facts b { font-weight: 700; }
  .facts svg { width: 12px; height: 12px; }
  .tour-title {
    position: absolute; top: 513px; height: 30px; margin: 0;
    padding: 0 10px 0 17px;
    background: var(--ink);
    font-weight: 300; font-size: 17.5px; line-height: 30px;
    white-space: nowrap;
  }
  .stops { position: absolute; top: 562px; margin: 0; padding: 0; list-style: none; font-size: 13.5px; line-height: 21.5px; }
  .stops li { position: relative; padding-left: 17px; white-space: nowrap; }
  .stops li::before {
    content: ""; position: absolute; left: 0; top: 5px; width: 12px; height: 12px;
    background: var(--ink);
  }
  .stops .plane { position: absolute; left: 1px; top: 6px; width: 10px; height: 10px; }
  .footer-band { position: absolute; left: 0; top: 818px; width: 1200px; height: 31px; background: var(--deep); }
</style>
</head>
<body>
<main class="spread">
  <header class="intro-strip">
    <p class="intro" style="left:10px">This is one of our most popular scenic tours because it showcases<br>Sydneys magnificent coastline and world famous beaches. The<br>Sydney coastal flight takes you past many well known coastal land-<br>marks and beaches such as Maroubra Beach</p>
    <p class="intro" style="left:413px">This is one of our most popular scenic tours because it showcases<br>Sydneys magnificent coastline and world famous beaches. The<br>Sydney coastal flight takes you past many well known coastal land-<br>marks and beaches such as Maroubra Beach</p>
    <p class="intro" style="left:807px">This is one of our most popular scenic tours because it showcases<br>Sydneys magnificent coastline and world famous beaches. The<br>Sydney coastal flight takes you past many well known coastal land-<br>marks and beaches such as Maroubra Beach</p>
  </header>

  <div class="photo photo--harbour" role="img" aria-label="Aerial view of the harbour bridge from a light aircraft wing"></div>
  <div class="photo photo--beach" role="img" aria-label="Sunny beach with surf and grassy foreshore"></div>
  <div class="photo photo--cliffs" role="img" aria-label="Sandstone rock pillars in the Blue Mountains at sunset"></div>

  <svg class="wave" viewBox="0 0 1200 110" preserveAspectRatio="none" aria-hidden="true">
    <path d="M0 48 C300 30 500 20 700 40 C900 60 1050 30 1200 20 L1200 110 L0 110 Z" fill="#3276b5"/>
    <path d="M0 56 C300 40 500 35 700 55 C900 75 1050 48 1200 36 L1200 110 L0 110 Z" fill="#ffffff"/>
    <path d="M0 64 C300 55 500 62 700 82 C900 94 1050 70 1200 56 L1200 110 L0 110 Z" fill="#33a6d7"/>
  </svg>

  <ul class="facts" style="left:195px">
    <li><svg viewBox="0 0 12 12"><circle cx="6" cy="6" r="5" fill="none" stroke="#fff" stroke-width="1.4"/><path d="M6 3v3h2" stroke="#fff" stroke-width="1.4" fill="none"/></svg><span><b>Duration:</b> 1 hour 20 mins</span></li>
    <li><svg viewBox="0 0 12 12"><path d="M1 6 6 1h5v5l-5 5z" fill="#fff"/><circle cx="8.5" cy="3.5" r="1" fill="#33a6d7"/></svg><span><b>Price:</b> $560 per aircraft</span></li>
  </ul>
  <ul class="facts" style="left:598px">
    <li><svg viewBox="0 0 12 12"><circle cx="6" cy="6" r="5" fill="none" stroke="#fff" stroke-width="1.4"/><path d="M6 3v3h2" stroke="#fff" stroke-width="1.4" fill="none"/></svg><span><b>Duration:</b> 1 hour 20 mins</span></li>
    <li><svg viewBox="0 0 12 12"><path d="M1 6 6 1h5v5l-5 5z" fill="#fff"/><circle cx="8.5" cy="3.5" r="1" fill="#33a6d7"/></svg><span><b>Price:</b> $560 per aircraft</span></li>
  </ul>
  <ul class="facts" style="left:1000px">
    <li><svg viewBox="0 0 12 12"><circle cx="6" cy="6" r="5" fill="none" stroke="#fff" stroke-width="1.4"/><path d="M6 3v3h2" stroke="#fff" stroke-width="1.4" fill="none"/></svg><span><b>Duration:</b> 1 hour 10 mins</span></li>
    <li><svg viewBox="0 0 12 12"><path d="M1 6 6 1h5v5l-5 5z" fill="#fff"/><circle cx="8.5" cy="3.5" r="1" fill="#33a6d7"/></svg><span><b>Price:</b> $475 per aircraft</span></li>
  </ul>

  <h2 class="tour-title" style="left:0">Sydney Harbour Scenic</h2>
  <h2 class="tour-title" style="left:400px">Sydney Coastal</h2>
  <h2 class="tour-title" style="left:801px;padding-left:25px">The Blue Mountains</h2>

  <svg width="0" height="0" style="position:absolute" aria-hidden="true">
    <symbol id="plane" viewBox="0 0 10 10"><path d="M9 1 1 4.5l3 1 .8 3 1.4-2 2 1z" fill="#fff"/></symbol>
  </svg>

  <ul class="stops" style="left:24px">
    <li><svg class="plane"><use href="#plane"/></svg>Parramatta City</li>
    <li><svg class="plane"><use href="#plane"/></svg>Hornsby</li>
    <li><svg class="plane"><use href="#plane"/></svg>Bahai Temple</li>
    <li><svg class="plane"><use href="#plane"/></svg>Sydney Harbour Bridge</li>
    <li><svg class="plane"><use href="#plane"/></svg>Quayside Concert Pavilion</li>
    <li><svg class="plane"><use href="#plane"/></svg>Manly</li>
    <li><svg class="plane"><use href="#plane"/></svg>Long Reef</li>
  </ul>
  <ul class="stops" style="left:428px">
    <li><svg class="plane"><use href="#plane"/></svg>Cambelltown</li>
    <li><svg class="plane"><use href="#plane"/></svg>Stanwell Park</li>
    <li><svg class="plane"><use href="#plane"/></svg>Entrance of Port Hacking</li>
    <li><svg class="plane"><use href="#plane"/></svg>Entrance of Botany Bay</li>
    <li><svg class="plane"><use href="#plane"/></svg>Famous Sydney Beaches including<br>Maroubra, Cooge, Bondi &amp; Manly</li>
    <li><svg class="plane"><use href="#plane"/></svg>Sydney Heads</li>
    <li><svg class="plane"><use href="#plane"/></svg>Long Reef</li>
  </ul>
  <ul class="stops" style="left:830px">
    <li><svg class="plane"><use href="#plane"/></svg>Katoomba</li>
    <li><svg class="plane"><use href="#plane"/></svg>The Three Sisters</li>
    <li><svg class="plane"><use href="#plane"/></svg>Warragamba Dam</li>
    <li><svg class="plane"><use href="#plane"/></svg>Prospect Resrvour</li>
  </ul>

  <div class="footer-band"></div>
</main>
</body>
</html>
```